Website Design for Harbor Guidance

I am looking to create a website to help military members who are currently serving or have served to have a mentor. The military does an awful job and providing or offering a mentor program. People need someone they can come to with career advice with promotions, networking, building resumes, and pinging ideas off of on the occasion. I want a place where active and separated military members can come to, sign up and pick a program of offerings that make sense. They would register annually, pay for a membership package (can choose up to three) and then get support they need. Annual registration fees would be as follows and they would need to send payment through Paypal or other electronic means (credit card, eft, paypal, echeck, whatever).

I envision some type of registration that centers around the packages offered - this will be where the revision comes in once the framework is completed.

I am looking for very creative designs, and content, given the above, with verbiage around mentorship program. Please be creative for the design, and also put together three packages and price points for them three packages - put together what it would include in each package. We can modify as necessary during revisions. Final design should communicate military members in uniform with corporate leaders, something warm and inviting are important. I also want the abiity to really get this adversited and in the market for people to stumble across it easily.

I have purchased the domain already - harborguidance.com

Target Market(s)

Military, Veterans

Number of Pages Required

1 page

Requirements
Must have
• Military member with corporate look
• Modern and wide
• Warm and inviting
• Registration with ability to collect through PayPal, eCheck, Credit Card, etc)
• Creative design and content for the website based on what is described in the description
• About Section which has information about leadership team
• Contact Us
• Register
• 3 creative packages of what would be included (design this and the content keeping in mind the description)
• Content and the framework
• Some type of packages to consider (just examples but also needs mentoring options:
• https://www.careerdraftsmithy.com/
• https://www.cvbeacon.com/
• We are not going to ba resume writing service but we will offer it as part of our solution - I really want it to be focused around mentorship for job development, professional advice, interacting with peers, managers, leaders (using military acronyms like Supervisors and Leaders NCO's, Officers, etc)
• Blog so we can post topics and interact and respond to questions people have etc

```html
<!DOCTYPE html>
<html lang="en">
<head>
<meta charset="utf-8">
<title>Harbor Guidance</title>
<link href="https://fonts.googleapis.com/css2?family=Lato:wght@300;400;700&display=swap" rel="stylesheet">
<style>
:root{
  --blue:#1f73c9;
  --blue-dark:#1b4f95;
  --blue-light:#4a9be6;
  --gold:#f9a602;
  --orange:#f07424;
  --ink:#1d1d1d;
  --grey:#6b6b6b;
  --line:#d9d9d9;
  --navy:#0e1827;
  --white:#ffffff;
}
*{margin:0;padding:0;box-sizing:border-box}
html,body{width:1200px;height:3051px;overflow:hidden}
body{font-family:'Lato',Arial,sans-serif;color:var(--ink);background:var(--white);position:relative}
.abs{position:absolute}

/* header */
.site-header{position:absolute;left:0;top:0;width:1200px;height:110px;background:var(--white)}
.brand{position:absolute;left:118px;top:30px;font-size:34px;font-weight:400;color:var(--blue)}
.top-actions{position:absolute;top:12px;left:588px;display:flex;gap:12px}
.btn-top{height:36px;padding:0 14px;font-size:13px;display:flex;align-items:center;border:2px solid var(--blue);color:var(--blue);background:var(--white)}
.btn-top.gold{background:var(--gold);border-color:var(--gold);color:var(--white)}
.btn-top.dark{background:var(--blue-dark);border-color:var(--blue-dark);color:var(--white);padding:0 20px}
.main-nav{position:absolute;top:66px;left:520px;display:flex;gap:30px;font-size:16px;color:var(--ink)}

/* hero */
.hero{position:absolute;left:0;top:110px;width:1200px;height:495px;background:linear-gradient(100deg,#f4f4f4 0%,#e9eaeb 45%,#dcdee0 100%)}
.hero-photo{position:absolute;left:540px;top:20px;width:470px;height:475px;background:linear-gradient(180deg,#b8b2a6 0%,#8f8a7c 55%,#6f6a5e 100%);border-radius:190px 190px 0 0;opacity:.85}
.hero h1{position:absolute;left:120px;top:130px;font-size:34px;font-weight:400;line-height:41px;color:#111}
.hero p{position:absolute;left:120px;top:226px;width:440px;font-size:16px;line-height:22px;color:var(--grey)}
.btn-start{position:absolute;left:120px;top:295px;width:162px;height:48px;background:var(--gold);color:var(--white);font-size:14px;font-weight:700;display:flex;align-items:center;justify-content:center;letter-spacing:.5px}
.arrow-round{position:absolute;width:48px;height:48px;border:2px solid #333;border-radius:50%;background:rgba(255,255,255,.6)}

/* offer */
.offer{position:absolute;left:0;top:605px;width:1200px;height:345px;background:linear-gradient(180deg,var(--blue-light) 0%,#2b7bd6 100%);color:var(--white)}
.section-title{font-size:26px;font-weight:400;text-align:center;letter-spacing:.5px}
.offer .section-title{position:absolute;top:42px;width:100%;color:var(--white)}
.offer-item{position:absolute;top:108px;width:220px;text-align:center}
.offer-icon{width:110px;height:110px;margin:0 auto;border-radius:50%;border:6px solid rgba(255,255,255,.25);background:var(--blue);display:flex;align-items:center;justify-content:center}
.offer-item h3{margin-top:18px;font-size:16px;font-weight:400;line-height:24px;text-transform:uppercase}

/* about */
.about-photo{position:absolute;left:110px;top:970px;width:500px;height:435px;background:linear-gradient(90deg,#3b4056 0%,#b9a08a 48%,#7d7356 70%,#5d5a45 100%);border-radius:220px 220px 0 0}
.about-text{position:absolute;left:662px;top:1040px;width:430px}
.about-text h2{font-size:32px;font-weight:400;color:#111;margin-bottom:20px}
.about-text p{font-size:13px;line-height:21px;color:var(--grey);margin-bottom:10px}
.btn-outline{display:flex;align-items:center;justify-content:center;border:2px solid var(--blue);color:var(--blue);font-size:14px;background:var(--white)}

/* packages */
.packages{position:absolute;left:0;top:1405px;width:1200px;height:470px;background:linear-gradient(180deg,#ececec 0%,#e6e2e0 50%,#efefef 100%)}
.packages .section-title{position:absolute;top:40px;width:100%;color:#111}
.pkg{position:absolute;top:143px;width:304px;height:274px;background:var(--white);border-top:4px solid var(--gold);box-shadow:0 2px 6px rgba(0,0,0,.08);text-align:center}
.pkg-icon{position:absolute;left:104px;top:-46px;width:96px;height:96px;border-radius:50%;background:var(--gold);display:flex;align-items:center;justify-content:center}
.pkg h3{margin-top:66px;font-size:18px;font-weight:700;color:#111}
.pkg .price{font-size:22px;color:var(--blue);margin-top:2px}
.pkg p{width:200px;margin:8px auto 0;font-size:12px;line-height:20px;color:var(--grey)}
.pkg-actions{position:absolute;left:12px;bottom:12px;display:flex;gap:12px}
.btn-buy{width:136px;height:42px;background:var(--blue-dark);color:var(--white);font-size:13px;display:flex;align-items:center;justify-content:center}
.btn-more{width:134px;height:42px;border:2px solid var(--gold);color:var(--gold);font-size:13px;display:flex;align-items:center;justify-content:center}

/* blogs */
.blogs .section-title{position:absolute;top:1920px;left:0;width:1200px;color:#333;font-size:30px}
.blog-card{position:absolute;background:var(--white);border:1px solid var(--line)}
.blog-img{position:absolute}
.date-tag{position:absolute;background:var(--blue-dark);color:var(--white);font-size:12px;padding:6px 12px}
.blog-card h4{font-size:17px;font-weight:400;color:#222}
.blog-card p{font-size:11px;line-height:17px;color:var(--grey)}
.btn-read{width:116px;height:30px;background:var(--gold);color:var(--white);font-size:12px;display:flex;align-items:center;justify-content:center}

/* contact */
.contact{position:absolute;left:0;top:2412px;width:1200px;height:436px;background:linear-gradient(180deg,#f07424 0%,#ee6f1f 100%)}
.contact .section-title{position:absolute;top:50px;width:100%;color:var(--white);font-size:28px}
.field{position:absolute;background:linear-gradient(180deg,#ffffff 0%,#ebebeb 100%);font-size:13px;color:#444;padding:0 14px;display:flex;align-items:center}
.field.area{align-items:flex-start;padding-top:14px}
.btn-send{position:absolute;left:520px;top:333px;width:166px;height:45px;background:var(--blue);color:var(--white);font-size:16px;display:flex;align-items:center;justify-content:center}

/* footer */
.site-footer{position:absolute;left:0;top:2848px;width:1200px;height:203px;background:var(--navy);color:var(--white);text-align:center}
.social{position:absolute;top:24px;left:530px;display:flex;gap:8px}
.social span{width:30px;height:30px;border:2px solid #8d96a5;border-radius:50%}
.foot-nav{position:absolute;top:78px;width:100%;display:flex;justify-content:center;gap:30px;font-size:16px}
.copy{position:absolute;top:112px;width:100%;font-size:12px;color:#cfd4dc}
.pay{position:absolute;top:148px;left:522px;display:flex;gap:18px}
.pay span{width:38px;height:24px;border-radius:3px;background:#dfe3ea}
</style>
</head>
<body>

<header class="site-header">
  <div class="brand">Harbor Guidance</div>
  <div class="top-actions">
    <div class="btn-top">Military Members Sign Up</div>
    <div class="btn-top gold">Active Member Sign up</div>
    <div class="btn-top dark">Register</div>
  </div>
  <nav class="main-nav">
    <span>Home</span><span>About Us</span><span>What we offer</span><span>Packages</span><span>Blogs</span><span>Contact</span>
  </nav>
</header>

<section class="hero">
  <div class="hero-photo" role="img" aria-label="Smiling service member in camouflage uniform holding a laptop, city towers behind"></div>
  <h1>Military Members Career<br>Advice with Promotions</h1>
  <p>Allamcorper est eget tempor cursus neque mi consect-etuer mi a ultricies massa est sed nisl Class</p>
  <div class="btn-start">START NOW</div>
  <div class="arrow-round" style="left:38px;top:214px">
    <svg width="44" height="44" viewBox="0 0 44 44"><path d="M25 14 L17 22 L25 30" fill="none" stroke="#333" stroke-width="2.5"/></svg>
  </div>
  <div class="arrow-round" style="left:1094px;top:214px">
    <svg width="44" height="44" viewBox="0 0 44 44"><path d="M19 14 L27 22 L19 30" fill="none" stroke="#333" stroke-width="2.5"/></svg>
  </div>
</section>

<section class="offer">
  <h2 class="section-title">WHAT WE OFFER</h2>
  <svg class="abs" style="left:98px;top:175px" width="20" height="30" viewBox="0 0 20 30"><path d="M14 4 L4 15 L14 26" fill="none" stroke="#fff" stroke-width="2.5"/></svg>
  <svg class="abs" style="left:1072px;top:175px" width="20" height="30" viewBox="0 0 20 30"><path d="M6 4 L16 15 L6 26" fill="none" stroke="#fff" stroke-width="2.5"/></svg>

  <div class="offer-item" style="left:158px">
    <div class="offer-icon">
      <svg width="54" height="54" viewBox="0 0 54 54" fill="none" stroke="#fff" stroke-width="2.4"><rect x="14" y="12" width="34" height="24"/><circle cx="9" cy="20" r="4"/><path d="M3 40v-8a6 6 0 0 1 12 0v2h14"/><path d="M20 20h20M20 27h14"/></svg>
    </div>
    <h3>Mentorship for job<br>development</h3>
  </div>
  <div class="offer-item" style="left:396px">
    <div class="offer-icon">
      <svg width="54" height="54" viewBox="0 0 54 54" fill="none" stroke="#fff" stroke-width="2.4"><rect x="28" y="6" width="20" height="14" rx="2"/><path d="M32 11h12M32 15h8"/><circle cx="22" cy="24" r="7"/><path d="M8 48v-6a10 10 0 0 1 10-10h8a10 10 0 0 1 10 10v6z"/></svg>
    </div>
    <h3>Professional<br>advice</h3>
  </div>
  <div class="offer-item" style="left:634px">
    <div class="offer-icon">
      <svg width="54" height="54" viewBox="0 0 54 54" fill="none" stroke="#fff" stroke-width="2.4"><circle cx="27" cy="27" r="16"/><path d="M27 4v6M27 44v6M4 27h6M44 27h6M11 11l4 4M39 39l4 4M11 43l4-4M39 15l4-4"/><circle cx="27" cy="23" r="4"/><path d="M19 35a8 8 0 0 1 16 0"/></svg>
    </div>
    <h3>Interacting with<br>peers</h3>
  </div>
  <div class="offer-item" style="left:870px">
    <div class="offer-icon">
      <svg width="54" height="54" viewBox="0 0 54 54" fill="none" stroke="#fff" stroke-width="2.4"><circle cx="27" cy="18" r="6"/><circle cx="13" cy="22" r="5"/><circle cx="41" cy="22" r="5"/><path d="M17 40a10 10 0 0 1 20 0M3 40a9 9 0 0 1 13-8M51 40a9 9 0 0 0-13-8"/></svg>
    </div>
    <h3>Managers &amp;<br>leaders</h3>
  </div>
</section>

<section class="about">
  <div class="about-photo" role="img" aria-label="Corporate leader in a suit beside a smiling soldier in uniform, arms crossed"></div>
  <div class="about-text">
    <h2>ABOUT US</h2>
    <p>Praesent elementum elit at tellus nec ultricies sit amet porttitor mattis enim In massa libero interdum nec interdum vel blandit sed nulla In ullamcorper est eget tempor cursus neque mi consectetuer</p>
    <p>massa est sed nisl Class aptent taciti sociosqu ad litora torquent per conubia nostra per inceptos hymenaeos Proin nulla arcu nonummy luctus dictum eget fermentum et lorem</p>
    <div class="btn-outline" style="width:148px;height:42px;margin-top:18px">READ MORE</div>
  </div>
</section>

<section class="packages" role="group" aria-label="Membership packages">
  <h2 class="section-title">OUR PACKAGES</h2>

  <div class="pkg" style="left:116px">
    <div class="pkg-icon">
      <svg width="44" height="44" viewBox="0 0 44 44" fill="none" stroke="#fff" stroke-width="2.4"><circle cx="22" cy="14" r="8"/><path d="M8 40v-4a10 10 0 0 1 10-10h8a10 10 0 0 1 10 10v4z"/><path d="M22 26v8"/></svg>
    </div>
    <h3>PROFESSIONAL</h3>
    <div class="price">$190</div>
    <p>Class aptent taciti sociosqu ad litora torquent per conubia nostra per inceptos hymenaeos Proin nulla arcu</p>
    <div class="pkg-actions"><div class="btn-buy">BUY NOW</div><div class="btn-more">LEARN MORE</div></div>
  </div>

  <div class="pkg" style="left:440px">
    <div class="pkg-icon">
      <svg width="44" height="44" viewBox="0 0 44 44"><circle cx="22" cy="12" r="8" fill="#fff"/><path d="M6 42v-8a12 12 0 0 1 12-12h8a12 12 0 0 1 12 12v8z" fill="#fff"/><path d="M20 22h4l-1 4 2 12-3 3-3-3 2-12z" fill="#f9a602"/></svg>
    </div>
    <h3>EXECUTIVE</h3>
    <div class="price">$270</div>
    <p>Class aptent taciti sociosqu ad litora torquent per conubia nostra per inceptos hymenaeos Proin nulla arcu</p>
    <div class="pkg-actions"><div class="btn-buy">BUY NOW</div><div class="btn-more">LEARN MORE</div></div>
  </div>

  <div class="pkg" style="left:764px">
    <div class="pkg-icon">
      <svg width="50" height="44" viewBox="0 0 50 44"><path d="M4 20c0-8 10-14 21-14s21 6 21 14l-6 6H10z" fill="#fff"/><rect x="10" y="26" width="30" height="6" fill="#fff"/><path d="M8 34h34l-4 5H12z" fill="#fff"/><circle cx="25" cy="16" r="3" fill="#f9a602"/></svg>
    </div>
    <h3>MILITARY</h3>
    <div class="price">$230</div>
    <p>Class aptent taciti sociosqu ad litora torquent per conubia nostra per inceptos hymenaeos Proin nulla arcu</p>
    <div class="pkg-actions"><div class="btn-buy">BUY NOW</div><div class="btn-more">LEARN MORE</div></div>
  </div>
</section>

<section class="blogs">
  <h2 class="section-title">OUR BLOGS</h2>

  <article class="blog-card" style="left:118px;top:1980px;width:472px;height:346px">
    <div class="blog-img" style="left:0;top:0;width:470px;height:204px;background:linear-gradient(90deg,#8d5f3f 0%,#4f6d8a 45%,#8c8778 100%)" role="img" aria-label="Mentor shaking hands with a service member across an office desk"></div>
    <div class="date-tag" style="left:0;top:176px">12 FEB 2018</div>
    <div style="position:absolute;left:24px;top:220px;width:420px">
      <h4>Etiam est nunc venenatis in tristique</h4>
      <p style="margin-top:8px">netus et malesuada fames ac turpis egestas Cras id elit Integer quis urna Ut ante enim dapibus malesuada fringilla eu condimen</p>
      <div class="btn-read" style="margin-top:12px">READ MORE</div>
    </div>
  </article>

  <article class="blog-card" style="left:606px;top:1980px;width:472px;height:168px">
    <div class="blog-img" style="left:0;top:0;width:216px;height:166px;background:linear-gradient(180deg,#9fb2c4 0%,#5b6470 60%,#2e3540 100%)" role="img" aria-label="Business leader in a suit in a bright office"></div>
    <div class="date-tag" style="left:0;top:140px">04 FEB 2018</div>
    <div style="position:absolute;left:240px;top:22px;width:210px">
      <h4>Blog Title here</h4>
      <p style="margin-top:8px">netus et malesuada fames ac turpis egestas Cras id elit Integer quis urna Ut ante enim dapibus malesua</p>
      <div class="btn-read" style="margin-top:10px">READ MORE</div>
    </div>
  </article>

  <article class="blog-card" style="left:606px;top:2156px;width:472px;height:168px">
    <div class="blog-img" style="left:0;top:0;width:216px;height:166px;background:linear-gradient(180deg,#7f8794 0%,#7a7460 55%,#4d4a3c 100%)" role="img" aria-label="Service member in uniform seated at a desk with a flag behind"></div>
    <div class="date-tag" style="left:0;top:140px">02 FEB 2018</div>
    <div style="position:absolute;left:240px;top:22px;width:210px">
      <h4>Blog Title here</h4>
      <p style="margin-top:8px">netus et malesuada fames ac turpis egestas Cras id elit Integer quis urna Ut ante enim dapibus malesua</p>
      <div class="btn-read" style="margin-top:10px">READ MORE</div>
    </div>
  </article>
</section>

<section class="contact">
  <svg class="abs" style="left:548px;top:0" width="104" height="22" viewBox="0 0 104 22"><path d="M0 0h104c-20 0-28 20-52 20S20 0 0 0z" fill="#fff"/><path d="M46 6l6 5 6-5" fill="none" stroke="#bbb" stroke-width="1.5"/></svg>
  <h2 class="section-title">CONTACT US</h2>
  <div class="field" style="left:236px;top:110px;width:360px;height:44px">First Name</div>
  <div class="field" style="left:608px;top:110px;width:364px;height:44px">Last Name</div>
  <div class="field" style="left:236px;top:162px;width:360px;height:44px">Email address</div>
  <div class="field" style="left:608px;top:162px;width:364px;height:44px">Phone Number</div>
  <div class="field area" style="left:236px;top:220px;width:736px;height:100px">Type Message</div>
  <div class="btn-send">SEND</div>
</section>

<footer class="site-footer">
  <div class="social" aria-label="Social links"><span></span><span></span><span></span><span></span></div>
  <nav class="foot-nav"><span>Home</span><span>About Us</span><span>What we offer</span><span>Packages</span><span>Blogs</span><span>Contact</span></nav>
  <div class="copy">© 2018 Company Name&nbsp; All right reserved</div>
  <div class="pay" aria-label="Accepted payment methods"><span></span><span></span><span></span><span></span></div>
</footer>

</body>
</html>
```